Using attached logo that has been created

Business card with logo that's attached. Maybe with water or the cartoon van in background. Looking for it to not be so plain and not too white.
Information to include;
Rodney Ashcombe
(555) 218-7730
Info@bramleypipeworks.example
www.bramleypipeworks.example
License # 4627195
Looking forward to the designs u come up with.
Thank you!
-Delphine
Target Market(s)
Plumbing
Industry/Entity Type
Plumbing
Contact Information for Business Card
Listed above

```html
<!DOCTYPE html>
<html lang="en">
<head>
<meta charset="utf-8">
<title>Bramley Pipeworks – Business Card</title>
<link href="https://fonts.googleapis.com/css2?family=Montserrat:wght@500;600;800&display=swap" rel="stylesheet">
<style>
  :root {
    --page-bg: #2b2b2d;
    --brand-blue: #0f57b3;
    --brand-yellow: #fbbf14;
    --card-white: #f4f5f6;
    --drop-grey: #d9dcdf;
    --text-white: #ffffff;
    --figure-skin: #c98a63;
    --figure-shirt: #1d5fc4;
    --figure-pants: #9d8763;
  }
  * { box-sizing: border-box; margin: 0; padding: 0; }
  html, body {
    width: 1200px;
    height: 1015px;
    overflow: hidden;
    background: var(--page-bg);
    font-family: "Montserrat", Arial, sans-serif;
  }
  .canvas {
    width: 1200px;
    height: 1015px;
    display: flex;
    flex-direction: column;
    align-items: center;
    justify-content: center;
    gap: 30px;
  }
  .card {
    position: relative;
    width: 800px;
    height: 457px;
    overflow: hidden;
    box-shadow: 0 10px 30px rgba(0,0,0,.45);
  }

  /* Front side */
  .card-front { background: var(--card-white); }
  .water-texture {
    position: absolute; inset: 0;
    background: radial-gradient(circle at 50% 50%, #ffffff 0%, var(--card-white) 55%, var(--drop-grey) 100%);
  }
  .front-figure {
    position: absolute;
    left: 290px; top: 40px;
    width: 220px; height: 300px;
    border-radius: 110px 110px 30px 30px;
    background: linear-gradient(180deg, var(--figure-skin) 0%, var(--figure-shirt) 35%, var(--figure-shirt) 60%, var(--figure-pants) 100%);
    opacity: .9;
  }
  .brand-lockup {
    position: absolute;
    left: 0; right: 0; top: 355px;
    display: flex;
    justify-content: center;
    align-items: center;
    gap: 14px;
  }
  .brand-dot {
    width: 22px; height: 22px;
    border-radius: 50%;
    background: var(--brand-yellow);
  }
  .brand-name {
    font-size: 40px;
    font-weight: 800;
    color: var(--brand-blue);
    letter-spacing: .5px;
  }

  /* Back side */
  .card-back { background: var(--brand-blue); }
  .yellow-band {
    position: absolute;
    left: 0; top: 0; bottom: 0;
    width: 175px;
    background: var(--brand-yellow);
  }
  .back-figure {
    position: absolute;
    left: 110px; top: 80px;
    width: 310px; height: 377px;
    border-radius: 155px 155px 0 0;
    background: linear-gradient(180deg, var(--figure-skin) 0%, var(--figure-skin) 25%, var(--figure-shirt) 42%, var(--figure-shirt) 70%, var(--figure-pants) 100%);
  }
  .contact-block {
    position: absolute;
    left: 450px; right: 20px; top: 105px;
    color: var(--text-white);
  }
  .person-name {
    font-size: 26px;
    font-weight: 800;
    color: var(--brand-yellow);
    letter-spacing: 1px;
    text-transform: uppercase;
    white-space: nowrap;
    margin-bottom: 20px;
  }
  .contact-list { list-style: none; }
  .contact-item {
    display: flex;
    align-items: center;
    gap: 10px;
    font-size: 17px;
    font-weight: 500;
    line-height: 1.6;
    white-space: nowrap;
  }
  .contact-icon { width: 18px; height: 18px; flex: none; }
  .license {
    margin-top: 30px;
    font-size: 22px;
    font-weight: 500;
  }
  .license-number { color: var(--brand-yellow); }
</style>
</head>
<body>
<main class="canvas">

  <section class="card card-front" aria-label="Card front">
    <div class="water-texture" role="img" aria-label="Background of water droplets on a white surface"></div>
    <div class="front-figure" role="img" aria-label="Cartoon plumber mascot holding a pipe wrench and a circular saw"></div>
    <div class="brand-lockup">
      <span class="brand-dot"></span>
      <span class="brand-name">Bramley Pipeworks &amp; More</span>
    </div>
  </section>

  <section class="card card-back" aria-label="Card back">
    <div class="yellow-band"></div>
    <div class="back-figure" role="img" aria-label="Cartoon plumber mascot with a pipe wrench on his shoulder and a circular saw in hand"></div>
    <div class="contact-block">
      <h1 class="person-name">Rodney Ashcombe</h1>
      <ul class="contact-list">
        <li class="contact-item">
          <svg class="contact-icon" viewBox="0 0 24 24" aria-hidden="true"><path fill="#fbbf14" d="M6.6 10.8a15.2 15.2 0 0 0 6.6 6.6l2.2-2.2c.3-.3.7-.4 1-.2 1.1.4 2.3.6 3.6.6.6 0 1 .4 1 1V20c0 .6-.4 1-1 1A17 17 0 0 1 3 4c0-.6.4-1 1-1h3.5c.6 0 1 .4 1 1 0 1.3.2 2.5.6 3.6.1.3 0 .7-.2 1z"/></svg>
          (555) 218-7730
        </li>
        <li class="contact-item">
          <svg class="contact-icon" viewBox="0 0 24 24" aria-hidden="true"><rect x="2" y="5" width="20" height="14" fill="#fbbf14"/><path d="M2 5l10 8 10-8" fill="none" stroke="#0f57b3" stroke-width="1.8"/></svg>
          Info@bramleypipeworks.example
        </li>
        <li class="contact-item">
          <svg class="contact-icon" viewBox="0 0 24 24" aria-hidden="true"><g fill="none" stroke="#fbbf14" stroke-width="2"><circle cx="12" cy="12" r="9"/><ellipse cx="12" cy="12" rx="4" ry="9"/><path d="M3 12h18M5 7h14M5 17h14"/></g></svg>
          www.bramleypipeworks.example
        </li>
      </ul>
      <p class="license">License # <span class="license-number">4627195</span></p>
    </div>
  </section>

</main>
</body>
</html>
```